BOLD & MINIMALIST DESIGN NEEDED

We want a very bold but minimalistic business card design that is impactful and utilizes both sides of the business card. Our current logo is included for your use.

We want bold fonts and good use of negative space. We don't want the logo to overpower the design.

Target Market(s)

Professionals who are building new commercial buildings.

Industry/Entity Type

Construction

Contact Information for Business Card

Name, Title, email, office phone, cell phone, website

Font styles to use
Serif
Sans Serif

Requirements
Must have
• Bold design!

```html
<!DOCTYPE html>
<html lang="en">
<head>
<meta charset="utf-8">
<title>Ridgewell Design + Build – Business Card</title>
<link rel="stylesheet" href="https://fonts.googleapis.com/css2?family=Montserrat:wght@800&family=Figtree:wght@400;500&display=swap">
<style>
  :root {
    --green: #84c341;
    --green-pale: #d3e9b8;
    --ink: #111111;
    --paper: #ffffff;
    --backdrop: #2a2a2a;
  }
  * { box-sizing: border-box; margin: 0; padding: 0; }
  html, body { width: 1200px; height: 1200px; overflow: hidden; }
  body { background: var(--backdrop); position: relative; font-family: "Figtree", sans-serif; }

  .card { position: absolute; width: 828px; height: 480px; overflow: hidden; }
  .card--front { left: 186px; top: 76px; background: var(--paper); }
  .card--back { left: 186px; top: 600px; background: var(--green); }

  .brand { position: absolute; text-align: center; font-family: "Montserrat", sans-serif; font-weight: 800; line-height: 1; }
  .brand__name { display: block; }
  .brand__line { display: block; }

  .card--front .brand { left: 40px; width: 340px; top: 190px; color: var(--ink); }
  .card--front .brand__name { font-size: 47px; letter-spacing: 0.5px; }
  .card--front .brand__line { font-size: 15px; letter-spacing: 7px; margin-top: 12px; }

  .divider { position: absolute; left: 420px; top: 128px; width: 2px; height: 202px; background: var(--green); }

  .person { position: absolute; left: 455px; top: 124px; }
  .person__name { font-family: "Montserrat", sans-serif; font-weight: 800; font-size: 32px; color: var(--green); line-height: 1.1; }
  .person__title { font-size: 21px; font-weight: 500; color: var(--ink); margin-top: 6px; }

  .contacts { position: absolute; left: 455px; top: 203px; list-style: none; }
  .contacts li { display: flex; align-items: center; height: 34px; font-size: 21px; font-weight: 500; color: var(--ink); }
  .contacts svg { width: 20px; height: 20px; margin-right: 14px; fill: var(--green); flex: none; }

  .address-band {
    position: absolute; left: 0; top: 410px; width: 100%; height: 42px;
    background: linear-gradient(90deg, var(--green-pale) 0%, var(--green) 42%, var(--green) 100%);
    display: flex; align-items: center; justify-content: center;
    font-size: 21px; font-weight: 500; color: var(--ink);
  }

  .card--back .brand { left: 0; width: 100%; top: 196px; color: var(--paper); }
  .card--back .brand__name { font-size: 80px; letter-spacing: 1px; }
  .card--back .brand__line { font-size: 26px; letter-spacing: 12px; margin-top: 16px; }
</style>
</head>
<body>
  <section class="card card--front">
    <div class="brand">
      <span class="brand__name">RIDGEWELL</span>
      <span class="brand__line">DESIGN + BUILD</span>
    </div>

    <div class="divider"></div>

    <div class="person">
      <h1 class="person__name">MARCUS VELDT</h1>
      <p class="person__title">Managing Director</p>
    </div>

    <ul class="contacts">
      <li>
        <svg viewBox="0 0 24 24" aria-hidden="true"><path d="M6.6 10.8a15.1 15.1 0 0 0 6.6 6.6l2.2-2.2c.3-.3.7-.4 1-.2 1.1.4 2.3.6 3.6.6.6 0 1 .4 1 1V20c0 .6-.4 1-1 1A17 17 0 0 1 3 4c0-.6.4-1 1-1h3.5c.6 0 1 .4 1 1 0 1.3.2 2.5.6 3.6.1.3 0 .7-.2 1z"/></svg>
        555-214-7730
      </li>
      <li>
        <svg viewBox="0 0 24 24" aria-hidden="true"><path d="M12 4C6 4 2 6 2 8.5V10h5V8.3c1.5-.4 3.3-.6 5-.6s3.5.2 5 .6V10h5V8.5C22 6 18 4 12 4zM6 11l-2 8h16l-2-8H6zm6 6.5a2.5 2.5 0 1 1 0-5 2.5 2.5 0 0 1 0 5z"/></svg>
        000 000 0000
      </li>
      <li>
        <svg viewBox="0 0 24 24" aria-hidden="true"><path d="M2 5h20v14H2z M3.5 6.5 12 13l8.5-6.5" fill="var(--green)"/><path d="M3 6.5 12 13l9-6.5" fill="none" stroke="#fff" stroke-width="1.4"/></svg>
        info@yourmail.com
      </li>
      <li>
        <svg viewBox="0 0 24 24" aria-hidden="true"><circle cx="12" cy="12" r="10"/><path d="M7 6c2 1 3 3 2 5s1 3 2 5M15 4c-1 2 0 3 2 4s2 3 1 5" fill="none" stroke="#fff" stroke-width="1.3"/></svg>
        www.yourwebsite.com
      </li>
    </ul>

    <div class="address-band">2450 Oakridge Blvd, Ste 200, Dallas, TX 75201</div>
  </section>

  <section class="card card--back">
    <div class="brand">
      <span class="brand__name">RIDGEWELL</span>
      <span class="brand__line">DESIGN + BUILD</span>
    </div>
  </section>
</body>
</html>
```